Frostvale Harborline LLC

we need a business card design

Industry/Entity Type

hvac

Contact Information for Business Card

my logo

Requirements
Must have
• my logo and same colors

```html
<!DOCTYPE html>
<html lang="en">
<head>
<meta charset="utf-8">
<title>Frostvale Harborline LLC — Business Card</title>
<link href="https://fonts.googleapis.com/css2?family=Montserrat:wght@400;500;700;800&display=swap" rel="stylesheet">
<style>
  :root {
    --brand-blue: #0b5fad;
    --deep-blue: #0a4f96;
    --sun-orange: #f5b341;
    --paper: #ffffff;
    --ink: #1d1d1d;
    --stage: #e9e6e1;
  }
  * { box-sizing: border-box; margin: 0; padding: 0; }
  html, body { width: 1200px; height: 931px; overflow: hidden; }
  body {
    background: var(--stage);
    font-family: "Montserrat", sans-serif;
    position: relative;
  }
  .card {
    position: absolute;
    width: 560px;
    height: 320px;
    border-radius: 18px;
    overflow: hidden;
    box-shadow: 0 10px 24px rgba(0,0,0,.18);
  }
  /* front */
  .card-front {
    left: 60px; top: 80px;
    background: var(--brand-blue);
    display: flex; align-items: center; justify-content: center; gap: 16px;
  }
  .front-mark {
    width: 34px; height: 34px; border-radius: 50%;
    background: var(--sun-orange);
    flex: none;
  }
  .front-name {
    color: var(--paper);
    font-weight: 800;
    font-size: 30px;
    line-height: 1.15;
    letter-spacing: .5px;
  }
  /* back */
  .card-back {
    left: 580px; top: 470px;
    background: var(--paper);
  }
  .back-brand {
    position: absolute; right: 40px; top: 40px;
    display: flex; align-items: center; gap: 10px;
    color: var(--brand-blue);
    font-weight: 800; font-size: 19px; line-height: 1.15;
    text-align: left;
  }
  .back-brand .mark {
    width: 22px; height: 22px; border-radius: 50%;
    background: var(--sun-orange); flex: none;
  }
  .rule-top {
    position: absolute; left: 200px; right: 40px; top: 150px;
    height: 1.5px; background: var(--brand-blue);
  }
  .address {
    position: absolute; right: 44px; top: 170px;
    font-size: 12px; line-height: 1.35; color: var(--ink); text-align: left;
  }
  .person { position: absolute; left: 40px; top: 150px; }
  .person-name {
    color: var(--brand-blue); font-weight: 800; font-size: 24px;
  }
  .person-title { font-size: 13px; color: var(--ink); margin-top: 2px; }
  .rule-person {
    width: 170px; height: 1.5px; background: var(--brand-blue); margin: 8px 0 10px;
  }
  .contacts { list-style: none; font-size: 13px; color: var(--ink); }
  .contacts li { display: flex; align-items: center; gap: 10px; margin-bottom: 5px; }
  .contacts svg { width: 14px; height: 14px; flex: none; }
  .bands { position: absolute; left: 0; bottom: 0; width: 560px; height: 40px; }
</style>
</head>
<body>
  <section class="card card-front" aria-label="Card front">
    <span class="front-mark"></span>
    <div class="front-name">Frostvale<br>Harborline LLC</div>
  </section>

  <section class="card card-back" aria-label="Card back">
    <div class="back-brand"><span class="mark"></span><span>Frostvale<br>Harborline LLC</span></div>
    <div class="rule-top"></div>
    <address class="address" style="font-style:normal">48 Willow Lane,<br>Brookfield, NY 13402</address>

    <div class="person">
      <div class="person-name">Daniel Brooks</div>
      <div class="person-title">Managing Director</div>
      <div class="rule-person"></div>
      <ul class="contacts">
        <li>
          <svg viewBox="0 0 14 14"><rect x="3.5" y="1" width="7" height="12" rx="1.5" fill="none" stroke="var(--sun-orange)" stroke-width="1.4"/></svg>
          +1 (555) 014-2290
        </li>
        <li>
          <svg viewBox="0 0 14 14"><rect x="1" y="3" width="12" height="8" fill="var(--sun-orange)"/><path d="M1 3l6 5 6-5" fill="none" stroke="#fff" stroke-width="1"/></svg>
          info@frostvaleharbor.com
        </li>
        <li>
          <svg viewBox="0 0 14 14"><circle cx="7" cy="7" r="6" fill="var(--sun-orange)"/><path d="M1 7h12M7 1c-3 3-3 9 0 12M7 1c3 3 3 9 0 12" fill="none" stroke="#fff" stroke-width=".8"/></svg>
          www.frostvaleharbor.com
        </li>
      </ul>
    </div>

    <svg class="bands" viewBox="0 0 560 40" aria-hidden="true">
      <polygon points="0,40 0,34 420,18 420,40" fill="var(--brand-blue)"/>
      <polygon points="428,40 428,14 560,0 560,40" fill="var(--sun-orange)"/>
    </svg>
  </section>
</body>
</html>
```